Luxury Wine Label for New Startup Winery

We need a wine label for our new winery startup. We have worked with a local designer but do not feel the resulting label / logo have the elevation required to present our brand as a luxury wine. Our winery is called "Quailbrook Vineyards" and we are focused on extremely high quality hand crafted artisan and estate wines from the Pacific Northwest.
We would like to see designs that utilize a tree line, or other imagery that represents the "Quailbrook" part of our company name. Another interesting feature could be wood grain.
A logo will be required based on your design so please design with this in mind:
This logo should be consistent with the wine bottle label design, and should be representative of our high end exclusive wine while giving a sense of place (Oregon/ Pacific Northwest.)
I will supply an image of the design we received from our local designer, PLEASE NOTE: in general we do like wood grain and tree line concepts but feel the execution was poorly done.
ATTN: Logo design should be suitable for use on: Bottles (Red wine/rose/white wine), Bussiness cards, vehicle signage, business signage, etc
P.S.:
If you have a design that is not outside the box we are still interested in seeing it.
Label is for a burgundy style bottle with a label height of 3.5 - 4" and a width of 3.5-4"
any label <= 4"x4" and >=3.5"x3.5" will be acceptable:
HOWEVER Width should be greater than or equal to height due to the bottle format
Target Market(s)
Wine enthusiasts with adequate discretionary budgets to afford $100 bottles of wine.
Industry/Entity Type
Wine / Winery
Requirements
Must have
- A sense of luxury, a feel of exclusivity, and a theme consistent with our product and brand name
Nice to have
- Tree line, wood grain or other wood themes. Serif fonts
Should not have
- anything cheesy, off topic, hard to read script fonts or anything that makes the label hard to read from a few feet away or too busy

```html
<!DOCTYPE html>
<html lang="en">
<head>
<meta charset="utf-8">
<title>Quailbrook Vineyards – Label Range</title>
<link href="https://fonts.googleapis.com/css2?family=Playfair+Display:wght@900&family=Didact+Gothic&family=Great+Vibes&display=swap" rel="stylesheet">
<style>
  :root {
    --page: #f4f4f4;
    --glass-white: #5f5a1c;
    --glass-red: #3a1418;
    --glass-gold: #efe3a0;
    --glass-rose: #f29a8c;
    --ink-light: #f2f2f2;
    --ink-dark: #3c3c3c;
    --ink-warm: #6b5a2a;
    --silver-1: #9a9a9a;
    --silver-2: #e6e6e6;
    --silver-3: #b8b8b8;
    --strip-ink: #222222;
    --photo-sky: #2e63b8;
    --photo-snow: #e8eef6;
  }
  * { box-sizing: border-box; margin: 0; padding: 0; }
  html, body { width: 1200px; height: 999px; overflow: hidden; }
  body { background: var(--page); position: relative; font-family: "Didact Gothic", sans-serif; }

  .label {
    position: absolute; width: 250px; height: 300px;
    border-radius: 6px; padding-top: 40px; text-align: center;
  }
  .label--white { left: 52px;  top: 455px; background: var(--glass-white); color: var(--ink-light); }
  .label--red   { left: 374px; top: 455px; background: var(--glass-red);   color: var(--ink-light); }
  .label--gold  { left: 672px; top: 390px; background: var(--glass-gold);  color: var(--ink-dark); }
  .label--rose  { left: 925px; top: 565px; background: var(--glass-rose);  color: var(--ink-dark); }

  .brand-name {
    font-family: "Playfair Display", serif; font-weight: 900;
    font-size: 21px; line-height: 25px; letter-spacing: 0.5px; text-transform: uppercase;
  }
  .tagline { margin-top: 26px; font-size: 12px; line-height: 16px; }
  .region  { font-size: 12.5px; line-height: 16px; letter-spacing: 0.3px; }
  .label--gold .tagline, .label--gold .region,
  .label--rose .tagline, .label--rose .region { color: var(--ink-warm); }

  .cask-strip {
    margin: 12px 10px 0; height: 86px; padding: 10px 10px 0;
    background: linear-gradient(100deg, var(--silver-1), var(--silver-2) 30%, var(--silver-3) 55%, var(--silver-2) 80%, var(--silver-1));
    color: var(--strip-ink); text-align: left;
  }
  .strip-cols { display: flex; }
  .strip-col { flex: 1; padding-left: 12px; }
  .strip-col + .strip-col { border-left: 1px solid #555; }
  .strip-title { font-size: 9.5px; }
  .strip-sub { font-size: 6.5px; margin-top: 4px; }
  .strip-box {
    margin-top: 2px; width: 80%; height: 13px; border: 1px solid #666;
    font-family: "Great Vibes", cursive; font-size: 11px; line-height: 12px; text-align: center;
  }
  .strip-foot { margin-top: 8px; display: flex; align-items: baseline; gap: 6px; }
  .strip-foot .small { font-size: 6px; }
  .strip-foot .volume { font-size: 11px; }

  .scene-photo {
    position: absolute; left: 385px; top: 856px; width: 161px; height: 123px;
    background: linear-gradient(180deg, var(--photo-sky) 0%, #6d96d8 35%, var(--photo-snow) 60%, #c9d6e6 100%);
  }
</style>
</head>
<body>

  <section class="label label--white">
    <h2 class="brand-name">Quailbrook<br>Vineyards</h2>
    <p class="tagline">HAND CRAFTED</p>
    <p class="region">Oregon | Pacific Northwest</p>
    <div class="cask-strip">
      <div class="strip-cols">
        <div class="strip-col"><p class="strip-title">SINGLE BARREL</p><p class="strip-sub">BARREL NUMBER</p><div class="strip-box"></div></div>
        <div class="strip-col"><p class="strip-title">CASK STRENGTH</p><p class="strip-sub">MASTER DISTILLER</p><div class="strip-box">Ellis Hart</div></div>
      </div>
      <div class="strip-foot"><span class="small">PRODUCT OF OREGON</span><span class="volume">750 ML</span><span class="small">40% ALC./VOL</span></div>
    </div>
  </section>

  <section class="label label--red">
    <h2 class="brand-name">Quailbrook<br>Vineyards</h2>
    <p class="tagline">HAND CRAFTED</p>
    <p class="region">Oregon | Pacific Northwest</p>
    <div class="cask-strip">
      <div class="strip-cols">
        <div class="strip-col"><p class="strip-title">SINGLE BARREL</p><p class="strip-sub">BARREL NUMBER</p><div class="strip-box"></div></div>
        <div class="strip-col"><p class="strip-title">CASK STRENGTH</p><p class="strip-sub">MASTER DISTILLER</p><div class="strip-box">Ellis Hart</div></div>
      </div>
      <div class="strip-foot"><span class="small">PRODUCT OF OREGON</span><span class="volume">750 ML</span><span class="small">40% ALC./VOL</span></div>
    </div>
  </section>

  <section class="label label--gold">
    <h2 class="brand-name">Quailbrook<br>Vineyards</h2>
    <p class="tagline">HAND CRAFTED</p>
    <p class="region">Oregon | Pacific Northwest</p>
    <div class="cask-strip">
      <div class="strip-cols">
        <div class="strip-col"><p class="strip-title">SINGLE BARREL</p><p class="strip-sub">BARREL NUMBER</p><div class="strip-box"></div></div>
        <div class="strip-col"><p class="strip-title">CASK STRENGTH</p><p class="strip-sub">MASTER DISTILLER</p><div class="strip-box">Ellis Hart</div></div>
      </div>
      <div class="strip-foot"><span class="small">PRODUCT OF OREGON</span><span class="volume">750 ML</span><span class="small">40% ALC./VOL</span></div>
    </div>
  </section>

  <section class="label label--rose">
    <h2 class="brand-name">Quailbrook<br>Vineyards</h2>
    <p class="tagline">HAND CRAFTED</p>
    <p class="region">Oregon | Pacific Northwest</p>
    <div class="cask-strip">
      <div class="strip-cols">
        <div class="strip-col"><p class="strip-title">SINGLE BARREL</p><p class="strip-sub">BARREL NUMBER</p><div class="strip-box"></div></div>
        <div class="strip-col"><p class="strip-title">CASK STRENGTH</p><p class="strip-sub">MASTER DISTILLER</p><div class="strip-box">Ellis Hart</div></div>
      </div>
      <div class="strip-foot"><span class="small">PRODUCT OF OREGON</span><span class="volume">750 ML</span><span class="small">40% ALC./VOL</span></div>
    </div>
  </section>

  <div class="scene-photo" role="img" aria-label="Snow-covered mountain peak behind a lodge and snowy evergreen trees under a blue sky"></div>

</body>
</html>
```